Brindlewick Solutions Ltd

I'd like to create a company letterhead for the attached logo in word format.

I'd like to emphasis the icon in large translucent state from the left corner and ensure that the letterhead colouring matches the colour palette of the current logo with a contrast so it's clear to see. I've attached a copy of our sister company page on the app for reference.

```html
<!DOCTYPE html>
<html lang="en">
<head>
<meta charset="utf-8">
<title>Brindlewick Solutions Ltd — Letterhead</title>
<link rel="stylesheet" href="https://fonts.googleapis.com/css2?family=Ubuntu:wght@400;500&display=swap">
<style>
  :root {
    --teal: #1fb3a2;
    --teal-light: #8fdcd2;
    --teal-faint: #e4f3f1;
    --grey: #a3a3a3;
    --text-grey: #7a7a7a;
    --paper: #ffffff;
    --backdrop: #e4e4e4;
  }
  html, body {
    margin: 0;
    width: 1200px;
    height: 800px;
    overflow: hidden;
    background: var(--backdrop);
    font-family: "Ubuntu", sans-serif;
  }
  .letterhead {
    position: absolute;
    left: 345px;
    top: 40px;
    width: 510px;
    height: 720px;
    background: var(--paper);
    box-shadow: 0 6px 18px rgba(0,0,0,0.12);
    overflow: hidden;
  }
  .letterhead__header, .letterhead__footer, .letterhead__watermark {
    position: absolute;
    left: 0;
    width: 510px;
  }
  .letterhead__header { top: 0; height: 90px; }
  .letterhead__footer { bottom: 0; height: 120px; }
  .letterhead__watermark { top: 180px; height: 380px; }
  .website {
    position: absolute;
    top: 9px;
    right: 18px;
    color: var(--paper);
    font-size: 9px;
    letter-spacing: 0.2px;
  }
  .brand {
    position: absolute;
    top: 104px;
    left: 30px;
    display: flex;
    align-items: center;
    gap: 8px;
    color: var(--teal);
    font-size: 19px;
    font-weight: 400;
  }
  .brand__dot {
    width: 24px;
    height: 24px;
    border-radius: 50%;
    background: var(--teal);
  }
  .address {
    position: absolute;
    left: 28px;
    bottom: 58px;
    font-size: 9px;
    line-height: 1.35;
    color: var(--text-grey);
  }
  .address__name { color: var(--teal); font-weight: 500; }
  .contact {
    position: absolute;
    left: 300px;
    bottom: 76px;
    font-size: 9px;
    line-height: 1.5;
    color: var(--text-grey);
    list-style: none;
    margin: 0;
    padding: 0;
  }
  .contact__item { display: flex; align-items: center; gap: 5px; }
  .contact__icon {
    width: 10px;
    height: 10px;
    border-radius: 50%;
    background: var(--teal);
    display: inline-flex;
    align-items: center;
    justify-content: center;
  }
</style>
</head>
<body>
  <main class="letterhead">
    <svg class="letterhead__header" viewBox="0 0 510 90" aria-hidden="true">
      <path d="M0 0 H250 C170 22 90 45 0 72 Z" fill="var(--grey)"/>
      <path d="M170 0 H510 V36 C410 40 300 52 210 70 C260 45 230 18 170 0 Z" fill="var(--teal)"/>
      <path d="M215 74 C320 52 420 44 510 42 V48 C420 50 320 58 215 74 Z" fill="var(--teal-light)"/>
    </svg>
    <span class="website">www.brindlewicksolutions.com</span>

    <div class="brand">
      <span class="brand__dot"></span>
      <span class="brand__name">Brindlewick Solutions Ltd</span>
    </div>

    <svg class="letterhead__watermark" viewBox="0 0 510 380" aria-hidden="true">
      <circle cx="80" cy="190" r="175" fill="var(--teal-faint)" opacity="0.8"/>
    </svg>

    <svg class="letterhead__footer" viewBox="0 0 510 120" aria-hidden="true">
      <circle cx="505" cy="50" r="32" fill="var(--teal)"/>
      <path d="M0 108 C160 98 340 80 510 60 V66 C340 86 160 104 0 114 Z" fill="var(--teal-light)"/>
      <path d="M0 114 C160 104 340 86 510 66 V120 H0 Z" fill="var(--teal)"/>
    </svg>

    <address class="address">
      <div class="address__name">Brindlewick Solutions Ltd</div>
      <div>Suite 214 Harbour Lane, State, Zip 4051, Country</div>
    </address>

    <ul class="contact">
      <li class="contact__item">
        <span class="contact__icon">
          <svg width="6" height="6" viewBox="0 0 10 10" aria-hidden="true"><path d="M2 1 L4 1 L5 3 L4 4 C4.5 5.5 5 6 6 6.5 L7 5.5 L9 6.5 V8.5 C9 9 8.5 9.5 8 9.5 C4 9 1 6 0.5 2 C0.5 1.5 1 1 2 1 Z" fill="#fff"/></svg>
        </span>
        (00) 01987 654 321
      </li>
      <li class="contact__item">
        <span class="contact__icon">
          <svg width="6" height="6" viewBox="0 0 10 10" aria-hidden="true"><rect x="0.5" y="2" width="9" height="6" fill="none" stroke="#fff" stroke-width="1.2"/><path d="M0.5 2 L5 5.5 L9.5 2" fill="none" stroke="#fff" stroke-width="1.2"/></svg>
        </span>
        hello@brindlewick.com
      </li>
    </ul>
  </main>
</body>
</html>
```